Remodeling brochure

We need an informative homeowner friendly brochure detailing our company and things we do. We are looking for an initial setup and ideas (# of pages, etc) and then we will send more content. We are uploading our logo design. We are a high end remodeling company specializing in kitchen & bath remodels. We sell ourselves on customer communication and attention to detail in our designs and remodels.

Target Market(s)

Residential homeowners

Contact Information for Business Card

Modern and attention grabbing

Requirements
Must have
• Name- Hearth & Tile Works<br/>Address- 718 NW Larkfield Drive Suite #207<br/> Ankeny, Iowa 50099<br/>Phone- 515-555-0184<br/>email-htworksiowa@example-mail.com

```html
<!DOCTYPE html>
<html lang="en">
<head>
<meta charset="utf-8">
<title>Hearth &amp; Tile Works — Brochure Cover</title>
<link rel="stylesheet" href="https://fonts.googleapis.com/css2?family=Montserrat:wght@300;500;800&display=swap">
<style>
  :root {
    --charcoal: #262826;
    --slate: #3f413f;
    --sky-blue: #2585c9;
    --royal-blue: #1e4fa8;
    --glow: #5e5f5e;
    --white: #ffffff;
  }
  html, body {
    margin: 0;
    padding: 0;
    width: 1200px;
    height: 927px;
    overflow: hidden;
    background: var(--charcoal);
  }
  .cover {
    position: relative;
    width: 1200px;
    height: 927px;
    background: var(--charcoal);
    overflow: hidden;
    font-family: "Montserrat", sans-serif;
  }
  .cover-art {
    position: absolute;
    inset: 0;
  }
  .brand {
    position: absolute;
    left: 69px;
    top: 68px;
    display: flex;
    align-items: center;
    gap: 16px;
  }
  .brand-mark {
    width: 58px;
    height: 58px;
    background: var(--sky-blue);
  }
  .brand-name {
    margin: 0;
    color: var(--sky-blue);
    font-weight: 500;
    font-size: 27px;
    letter-spacing: 0.5px;
    text-transform: uppercase;
  }
  .tagline {
    position: absolute;
    left: 57px;
    top: 757px;
    margin: 0;
    color: var(--white);
    line-height: 1;
  }
  .tagline-lead,
  .tagline-tail {
    display: block;
    font-weight: 300;
    font-size: 30px;
    letter-spacing: 0.3px;
  }
  .tagline-focus {
    display: block;
    color: var(--sky-blue);
    font-weight: 800;
    font-size: 54px;
    letter-spacing: 0.5px;
    margin: 4px 0 2px;
  }
</style>
</head>
<body>
  <main class="cover">
    <svg class="cover-art" width="1200" height="927" viewBox="0 0 1200 927" aria-hidden="false">
      <defs>
        <radialGradient id="brand-glow" cx="0.5" cy="0.3" r="0.6">
          <stop offset="0" stop-color="var(--glow)"/>
          <stop offset="1" stop-color="var(--charcoal)" stop-opacity="0"/>
        </radialGradient>
        <linearGradient id="kitchen-tones" x1="0" y1="0" x2="0" y2="1">
          <stop offset="0" stop-color="#f2f2f1"/>
          <stop offset="0.45" stop-color="#e4e2de"/>
          <stop offset="0.55" stop-color="#c9b497"/>
          <stop offset="0.7" stop-color="#8a8a88"/>
          <stop offset="1" stop-color="#5a5a5a"/>
        </linearGradient>
      </defs>
      <rect class="brand-glow" x="100" y="0" width="290" height="190" fill="url(#brand-glow)"/>
      <polygon class="accent-strip" points="780,57 857,57 819,128 739,128" fill="var(--royal-blue)"/>
      <polygon class="accent-strip" points="739,807 819,807 860,876 780,876" fill="var(--royal-blue)"/>
      <polygon class="chevron-slate" points="582,128 665,128 458,467 662,807 582,807 377,467" fill="var(--slate)"/>
      <polygon class="chevron-blue" points="665,128 819,128 613,467 819,807 662,807 458,467" fill="var(--sky-blue)"/>
      <polygon class="feature-photo" role="img" aria-label="Photo of a bright remodeled kitchen with white cabinets, butcher-block counters and a black and white checkered floor" points="893,0 1200,0 1200,927 893,927 613,467" fill="url(#kitchen-tones)"/>
    </svg>

    <header class="brand">
      <div class="brand-mark"></div>
      <p class="brand-name">Hearth &amp; Tile Works</p>
    </header>

    <h1 class="tagline">
      <span class="tagline-lead">SPECIALIZING IN</span>
      <span class="tagline-focus">KITCHEN &amp; BATH</span>
      <span class="tagline-tail">REMODELS</span>
    </h1>
  </main>
</body>
</html>
```